Pawn & Gun store business card design

Hello! We would like a new business card design for our pawn & gun store. We loan money on items of value and sell firearms, jewelry, electronics & more.

Card will need to have the following information:

Business name - Prairie Nickel Pawn & Gun
Address - 2417 Hwy 53 S. Suite C Cedar Hollow, TX 75246
Employees name - Darren Kellum
Phone number - 972-613-8840
Email - PrairieNickelPawn@Mailvera.com
Website - PrairieNickelPawn.com

Somewhere on the card we would like it to say "Offering 10 Month Layaway!" & "We buy & loan on anything of value!". Our main store color is orange (please see logo). Logo does not have to be on the business card but it can be. Would like the back to have an area to write a note on the back. We like vintage things like old coins, collectables, firearms and more so think about this in the design. We want a business card as unique as our store!

Colors

Designer to choose colors to be used in the design.

Requirements
Nice to have
• Vintage Style

```html
<!DOCTYPE html>
<html lang="en">
<head>
<meta charset="utf-8">
<title>Prairie Nickel Pawn &amp; Gun – Business Card</title>
<link rel="stylesheet" href="https://fonts.googleapis.com/css2?family=Oswald:wght@300;400;600&display=swap">
<style>
  :root {
    --backdrop: #c9c9cb;
    --kraft: #d2b488;
    --kraft-dark: #c6a675;
    --ink: #3b2416;
    --edge-orange: #e0622a;
  }
  * { margin: 0; padding: 0; box-sizing: border-box; }
  html, body { width: 1200px; height: 800px; overflow: hidden; }
  body {
    background: var(--backdrop);
    font-family: "Oswald", sans-serif;
    color: var(--ink);
    display: flex;
    flex-direction: column;
    align-items: center;
    justify-content: center;
    gap: 36px;
  }
  .card {
    position: relative;
    width: 600px;
    height: 343px;
    background: radial-gradient(ellipse at 40% 40%, var(--kraft) 0%, var(--kraft-dark) 100%);
    border-bottom: 3px solid var(--edge-orange);
    border-right: 3px solid var(--edge-orange);
    text-transform: uppercase;
  }
  /* Front */
  .card-front .holder-name {
    position: absolute;
    right: 290px;
    top: 147px;
    font-size: 30px;
    line-height: 30px;
    font-weight: 600;
    letter-spacing: 1px;
    white-space: nowrap;
  }
  .card-front .divider {
    position: absolute;
    left: 326px;
    top: 118px;
    width: 1.5px;
    height: 88px;
    background: var(--ink);
  }
  .card-front .contact-block {
    position: absolute;
    left: 342px;
    top: 117px;
    font-style: normal;
    font-size: 12.5px;
    font-weight: 300;
    line-height: 18px;
    letter-spacing: 0.3px;
    white-space: nowrap;
  }
  .card-front .contact-block .business-name { font-weight: 600; }
  .card-front .offer {
    position: absolute;
    left: 342px;
    top: 250px;
    font-size: 12.5px;
    font-weight: 300;
    line-height: 18px;
    letter-spacing: 0.3px;
    white-space: nowrap;
  }
  .card-front .offer .layaway { font-weight: 600; }
  /* Back */
  .card-back {
    display: flex;
    align-items: center;
    justify-content: center;
  }
  .card-back .brand {
    display: flex;
    align-items: center;
    gap: 12px;
  }
  .card-back .brand-mark {
    width: 18px;
    height: 18px;
    background: var(--edge-orange);
  }
  .card-back .brand-name {
    font-size: 30px;
    font-weight: 600;
    letter-spacing: 1px;
    color: var(--ink);
  }
</style>
</head>
<body>
  <section class="card card-front" aria-label="Business card front">
    <h1 class="holder-name">Darren Kellum</h1>
    <div class="divider"></div>
    <address class="contact-block">
      <div class="business-name">Prairie Nickel Pawn &amp; Gun</div>
      <div>2417 Hwy 53 S. Suite C Cedar Hollow, TX 75246</div>
      <div>972-613-8840</div>
      <div>PrairieNickelPawn@Mailvera.com</div>
      <div>www.PrairieNickelPawn.com</div>
    </address>
    <div class="offer">
      <div class="layaway">Offering 10 Month Layaway</div>
      <div>We buy &amp; loan on anything of value</div>
    </div>
  </section>

  <section class="card card-back" aria-label="Business card back">
    <div class="brand">
      <span class="brand-mark"></span>
      <span class="brand-name">Prairie Nickel Pawn</span>
    </div>
  </section>
</body>
</html>
```